Digital Billboard Design: Winter Sales Event

I own a boutique furniture store in Calgary, AB (larkhollowhome.ca) and I am looking to advertise our winter sale event on a new curved digital billboard (specs attached including required file type).

I have this billboard rented for 52-weeks so I will be looking to change the design every 4-weeks (i.e. this is intended to be an ongoing project).

The objective of this first billboard is to raise awareness around our annual winter sales event. The store itself is only a few blocks from the billboard so those commuting into downtown are just a short drive from the store.

I am looking for a fresh, clean, contemporary look that will grab your attention as you drive into downtown Calgary without presenting to much info so as to be distracting (and overwhelming -- the billboard does not need to contain all info on my current marketing material). I should also note that the store caters to a higher-end, more sophisticated clientele so the graphics need to reflect the brand (i.e. we are not Brenton Furniture or Couch Depot!).

I have attached three files:

Billboard specs
Current marketing material advertising sale (and all relevant data)
An idea that is from an American furniture store that I think is interesting

Target Market(s)

Upper middle class, sophisticated client who appreciates the finer things in life.

Industry/Entity Type

Furniture Store

Font styles to use
Sans Serif

Requirements
Must have
• Company Logo
• Winter Sales Event - 20 to 60% off
• Address: 2417 14th Ave SW
Nice to have
• Image of furniture -- see our website www.larkhollowhome.ca -- any photo from this site can be used
Should not have
• Too much text or visual distration

```html
<!DOCTYPE html>
<html lang="en">
<head>
<meta charset="utf-8">
<title>Winter Sales Event Billboard – Lark Hollow Home</title>
<link rel="stylesheet" href="https://fonts.googleapis.com/css2?family=Open+Sans:wght@300;400;600;700;800&display=swap">
<style>
  :root {
    --page-bg: #eceeef;
    --board-dark: #4f5862;
    --board-mid: #646d78;
    --board-light: #8a929b;
    --glow: rgba(220, 224, 228, 0.35);
    --text: #ffffff;
    --rule: rgba(255, 255, 255, 0.55);
    --photo-light: #d9d3c6;
    --photo-mid: #a89f8e;
    --photo-dark: #3b3430;
  }

  * { margin: 0; padding: 0; box-sizing: border-box; }

  html, body {
    width: 1145px;
    height: 1200px;
    overflow: hidden;
    background: var(--page-bg);
  }

  .billboard {
    position: absolute;
    left: 40px;
    top: 362px;
    width: 1065px;
    height: 476px;
    overflow: hidden;
    color: var(--text);
    font-family: "Open Sans", Arial, sans-serif;
    background:
      radial-gradient(ellipse 40% 60% at 88% 55%, var(--glow), transparent 70%),
      radial-gradient(ellipse 30% 40% at 62% 85%, rgba(200, 204, 208, 0.22), transparent 70%),
      linear-gradient(100deg, var(--board-dark) 0%, var(--board-mid) 55%, var(--board-light) 100%);
  }

  .headline,
  .offer,
  .brand-name,
  .store-address,
  .product-lines {
    position: absolute;
    left: 28px;
    line-height: 1;
    white-space: nowrap;
  }

  .headline {
    top: 46px;
    font-size: 64px;
    font-weight: 300;
    letter-spacing: 0.5px;
  }
  .headline strong { font-weight: 800; }

  .offer {
    top: 122px;
    font-size: 66px;
    font-weight: 800;
  }
  .offer .offer-to {
    font-size: 50px;
    font-weight: 400;
  }

  .divider {
    position: absolute;
    left: 30px;
    top: 199px;
    width: 578px;
    height: 2px;
    background: var(--rule);
  }

  .brand-name {
    top: 229px;
    font-size: 41px;
    font-weight: 300;
    letter-spacing: 3px;
  }

  .store-address {
    top: 295px;
    font-size: 39px;
    font-weight: 600;
  }

  .product-lines {
    top: 345px;
    font-size: 41px;
    font-weight: 600;
    line-height: 52px;
  }

  .furniture-photo {
    position: absolute;
    left: 560px;
    top: 150px;
    width: 450px;
    height: 326px;
    background:
      linear-gradient(180deg, transparent 0%, transparent 78%, var(--photo-dark) 78%, var(--photo-dark) 100%),
      linear-gradient(160deg, var(--photo-light) 0%, var(--photo-mid) 100%);
    border-radius: 6px 6px 0 0;
    opacity: 0.95;
  }
</style>
</head>
<body>
  <section class="billboard">
    <h1 class="headline">WINTER <strong>SALES</strong> EVENT</h1>
    <p class="offer">SAVE 20 <span class="offer-to">TO</span> 60%</p>
    <div class="divider"></div>
    <p class="brand-name">LARK HOLLOW HOME</p>
    <p class="store-address">2417 14TH AVE SW</p>
    <p class="product-lines">Furniture, Lighting,<br>Accessories</p>
    <div class="furniture-photo" role="img" aria-label="Photo of an upholstered cream bed with a curved headboard and white bedding"></div>
  </section>
</body>
</html>
```